Design and Renovation Company Luxury Business Card

I want to create a luxury business card for a Design and Renovation Firm . We will use our current logo. The company name is 528BUILDA. We do not want anything standard. We need a very unique concept.
Please see uploaded inspiration. I really like the textured paper option. I would like the card to be thick with debossing, and/or embossing options. The logo has orange in it but I would like to see the card with and without the orange. I think the orange may make the company feel less high-end. The goal is to elevate the logo not match its vibe per se of the logo. We want something very unique, not standard at all!
I would like a space for :
Logo,
Name,
Position,
Email,
Office number,
Website Address,
Business Address,
Thank you!
Have fun!
Target Market(s)
Home owners Age 35 +
Industry/Entity Type
Design and Renovation
Contact Information for Business Card
Logo, Name, Position, Email, Office number, Website Address, Business Address,.
Colors
Designer to choose colors to be used in the design.
Requirements
Must have
- A luxury designer feel. Must be black or dark grey but open to other luxury ideas.
Nice to have
- Gold, silver, black embossing or debossing. Textured paper design.
Should not have
- A cheap look and feel.

```html
<!DOCTYPE html>
<html lang="en">
<head>
<meta charset="utf-8">
<title>528BUILDA Business Card</title>
<link rel="stylesheet" href="https://fonts.googleapis.com/css2?family=Montserrat:wght@400;500;700&display=swap">
<style>
  :root {
    --backdrop: #262626;
    --card: #1a1a1a;
    --card-edge: #f28c1b;
    --accent: #f28c1b;
    --ink: #ffffff;
    --ink-soft: #d9d9d9;
    --tile-light: #6a6a6a;
    --tile-dark: #0a0a0a;
  }
  * { box-sizing: border-box; margin: 0; padding: 0; }
  html, body { width: 1200px; height: 801px; overflow: hidden; }
  body {
    background: var(--backdrop);
    font-family: "Montserrat", sans-serif;
    color: var(--ink);
    display: flex;
    align-items: center;
    justify-content: center;
    gap: 60px;
  }
  .card {
    position: relative;
    width: 525px;
    height: 300px;
    background: var(--card);
    border-radius: 22px;
    border-bottom: 4px solid var(--card-edge);
    box-shadow: 0 14px 30px rgba(0,0,0,.45);
    overflow: hidden;
  }
  .company-name {
    font-weight: 500;
    letter-spacing: 0;
    color: var(--ink);
    white-space: nowrap;
  }
  /* front */
  .card-front .company-name { position: absolute; left: 40px; top: 112px; font-size: 28px; }
  .holder { position: absolute; right: 40px; top: 34px; text-align: right; }
  .holder-name { color: var(--accent); font-weight: 700; font-size: 20px; }
  .holder-role { color: var(--ink-soft); font-size: 11px; margin-top: 3px; letter-spacing: .04em; }
  .accent-tile {
    position: absolute; right: 50px; top: 110px;
    width: 110px; height: 110px; border-radius: 4px;
    background: linear-gradient(160deg, var(--tile-light), var(--tile-dark));
  }
  .contact { position: absolute; left: 40px; bottom: 26px; font-size: 11px; line-height: 1.5; color: var(--ink-soft); }
  .contact-address { margin-bottom: 10px; }
  .contact-row { display: flex; align-items: center; gap: 8px; }
  .contact-row svg { width: 11px; height: 11px; fill: var(--accent); flex: none; }
  /* back */
  .card-back { display: flex; align-items: center; justify-content: center; }
  .card-back .company-name { font-size: 44px; }
</style>
</head>
<body>
  <section class="card card-front" aria-label="Card front">
    <p class="company-name">528BUILDA</p>
    <div class="holder">
      <p class="holder-name">Daniel Harper</p>
      <p class="holder-role">Managing Director</p>
    </div>
    <div class="accent-tile" role="img" aria-label="Decorative glossy tile"></div>
    <div class="contact">
      <p class="contact-address">415 Elm Park Ave, #112<br>Riverton, OH 430571</p>
      <p class="contact-row">
        <svg viewBox="0 0 24 24"><path d="M6.6 10.8a15 15 0 0 0 6.6 6.6l2.2-2.2a1 1 0 0 1 1-.25 11.4 11.4 0 0 0 3.6.57 1 1 0 0 1 1 1V20a1 1 0 0 1-1 1A17 17 0 0 1 3 4a1 1 0 0 1 1-1h3.5a1 1 0 0 1 1 1c0 1.25.2 2.45.57 3.57a1 1 0 0 1-.25 1z"/></svg>
        555-318-0427
      </p>
      <p class="contact-row">
        <svg viewBox="0 0 24 24"><path d="M2 5h20v14H2zm2 2v.5l8 5 8-5V7z"/></svg>
        hello@528builda.com
      </p>
      <p class="contact-row">
        <svg viewBox="0 0 24 24"><circle cx="12" cy="12" r="10"/></svg>
        www.528builda.com
      </p>
    </div>
  </section>

  <section class="card card-back" aria-label="Card back">
    <p class="company-name">528BUILDA</p>
  </section>
</body>
</html>
```